Pine Ledge Traders, LLC- Global Beverage Company with 100% Cold Chain Logistics

Hey All, My Name is Dale, I am a young business owner in a competitive export space, but my niche is that I am shipping all of my beer around the world, "100% Cold Chain". This model is more costly, but it protects the integrity of the beer itself and will give folks in foreign countries the best representation of what US Craft Beer has to offer.

I am not a branding guy and don't claim to be one, I am a salesperson first, and will be referring to all of you to create something great that will be memorable.

I am looking for a basic Business Card Design for my Craft Beer Export company. I sell US Craft Beer in several countries around the globe. Austrailia, China, Taiwan, Chile, France, New Zealand... to name a few.

I am looking for a sleek, modern, and fresh design. Quickly!

Thanks for your consideration!

Cheers,

Dale

Target Market(s)

International

Contact Information for Business Card

Dale Corrigan
Founder- Roaming Hops Guy
Dale@PineLedgeTraders.example
@RoamingHopsGuy- Instagram only
www.Pineledgetraders.example
@PineLedgeTradersAU- Instagram Only

Font styles to use
Serif

Colors
0592cd
ffffff

Requirements
Must have
• Name-
• Title-
• Email-
• Social Media Handle-
• Company Website-
Nice to have
• Nice Logo/ Images on Card
Should not have
• Tacky Beer Images

```html
<!DOCTYPE html>
<html lang="en">
<head>
<meta charset="utf-8">
<title>Pine Ledge Traders – Business Card</title>
<link rel="stylesheet" href="https://fonts.googleapis.com/css2?family=Cinzel:wght@500&family=Roboto:wght@400&display=swap">
<style>
  :root {
    --brand-blue: #0592cd;
    --paper: #ffffff;
    --stage: #676767;
    --ink-grey: #5d5d5d;
    --mark-grey: #97a3ab;
  }
  * { margin: 0; padding: 0; box-sizing: border-box; }
  html, body { width: 1200px; height: 802px; overflow: hidden; }
  body { background: var(--stage); position: relative; font-family: "Roboto", Arial, sans-serif; }

  .card {
    position: absolute;
    top: 274px;
    width: 442px;
    height: 265px;
  }
  .card--front { left: 136px; background: var(--paper); }
  .card--back { left: 624px; background: var(--brand-blue); }

  .brand {
    position: absolute;
    display: flex;
    flex-direction: column;
    align-items: center;
    transform: translateX(-50%);
  }
  .brand__square { width: 46px; height: 46px; }
  .brand__name {
    font-family: "Cinzel", Georgia, serif;
    font-weight: 500;
    text-transform: uppercase;
    white-space: nowrap;
    margin-top: 12px;
    letter-spacing: 0.5px;
  }
  .card--front .brand { left: 110px; top: 82px; }
  .card--front .brand__square { background: var(--brand-blue); }
  .card--front .brand__name { color: var(--brand-blue); font-size: 18px; }
  .card--back .brand { left: 221px; top: 66px; }
  .card--back .brand__square { background: var(--paper); width: 56px; height: 56px; }
  .card--back .brand__name { color: var(--paper); font-size: 23px; margin-top: 16px; }

  .contact { position: absolute; left: 223px; top: 75px; color: var(--ink-grey); }
  .contact__name {
    font-family: "Cinzel", Georgia, serif;
    font-weight: 500;
    font-size: 18px;
    color: var(--brand-blue);
    line-height: 1;
    letter-spacing: 0.3px;
  }
  .contact__title { font-size: 12.5px; margin-top: 3px; }
  .contact__list { list-style: none; margin-top: 11px; font-size: 12.5px; }
  .contact__list li { display: flex; align-items: center; height: 16px; }
  .contact__list li.contact__social { margin-top: 16px; }
  .contact__icon { width: 12px; height: 12px; margin-right: 6px; flex: none; }
</style>
</head>
<body>
  <section class="card card--front" aria-label="Card front">
    <div class="brand">
      <span class="brand__square"></span>
      <span class="brand__name">Pine Ledge Traders</span>
    </div>
    <div class="contact">
      <h1 class="contact__name">Dale Corrigan</h1>
      <p class="contact__title">Founder - Roaming Hops Guy</p>
      <ul class="contact__list">
        <li>
          <svg class="contact__icon" viewBox="0 0 12 12" aria-hidden="true">
            <rect x="0.5" y="2" width="11" height="8" fill="#0592cd"/>
            <path d="M1 2.5 L6 6.5 L11 2.5" fill="none" stroke="#fff" stroke-width="1"/>
          </svg>
          Dale@PineLedgeTraders.example
        </li>
        <li>
          <svg class="contact__icon" viewBox="0 0 12 12" aria-hidden="true">
            <circle cx="6" cy="6" r="5.5" fill="#0592cd"/>
            <path d="M1 6 H11 M6 0.5 V11.5" stroke="#fff" stroke-width="0.9"/>
          </svg>
          www.Pineledgetraders.example
        </li>
        <li class="contact__social">
          <svg class="contact__icon" style="width:16px;height:16px" viewBox="0 0 16 16" aria-hidden="true">
            <circle cx="8" cy="8" r="7.2" fill="none" stroke="#0592cd" stroke-width="1.1"/>
          </svg>
          @RoamingHopsGuy
        </li>
      </ul>
    </div>
  </section>

  <section class="card card--back" aria-label="Card back">
    <div class="brand">
      <span class="brand__square"></span>
      <span class="brand__name">Pine Ledge Traders</span>
    </div>
  </section>
</body>
</html>
```